Business cards for Harbourline Supply Pty Ltd that import building products into Australia from China
Target Market(s)
Business to Business
Industry/Entity Type
Business
Contact Information for Business Card
Front: Logo and Business Name
Rear:
Desmond Varrick
General Manager
Mobile: 0427 561 394
email: dessie@harbourlinesupply.com.au
alternative email: dessie@outbackworks.com.au
web: www.harbourlinesupply.com.au
Geelong, Townsville and Launceston
Colors
ec1f27
fbee3d

```html
<!DOCTYPE html>
<html lang="en">
<head>
<meta charset="utf-8">
<title>Harbourline Supply Pty Ltd – Business Cards</title>
<link rel="stylesheet" href="https://fonts.googleapis.com/css2?family=Montserrat:wght@400;500;600;700&display=swap">
<style>
  :root {
    --brand-red: #ec1f27;
    --brand-yellow: #fbee3d;
    --card-black: #050505;
    --card-white: #ffffff;
    --ink-grey: #4a4a4c;
    --mark-grey: #4b4b4d;
    --backdrop: #e4e4e6;
  }
  * { margin: 0; padding: 0; box-sizing: border-box; }
  html, body { width: 1200px; height: 864px; overflow: hidden; }
  body {
    background: var(--backdrop);
    font-family: "Montserrat", sans-serif;
    display: flex;
    flex-direction: column;
    align-items: center;
    justify-content: center;
    gap: 48px;
  }
  .card {
    position: relative;
    width: 620px;
    height: 354px;
    border-radius: 22px;
    overflow: hidden;
    box-shadow: 0 10px 28px rgba(0,0,0,0.18);
  }

  /* Front */
  .card-front { background: var(--card-black); }
  .front-brand {
    position: absolute;
    left: 0; right: 0; top: 128px;
    display: flex;
    align-items: center;
    justify-content: center;
    gap: 16px;
  }
  .front-brand .brand-dot {
    width: 22px; height: 22px;
    background: var(--brand-yellow);
  }
  .brand-name {
    color: var(--brand-red);
    font-weight: 700;
    letter-spacing: 0.06em;
    text-transform: uppercase;
    line-height: 1.1;
  }
  .front-brand .brand-name { font-size: 30px; }
  .front-brand .brand-name span { display: block; font-size: 17px; letter-spacing: 0.18em; }
  .city-list {
    position: absolute;
    left: 0; right: 0; bottom: 52px;
    display: flex;
    justify-content: center;
    align-items: center;
    gap: 9px;
    color: #fff;
    font-size: 14px;
    font-weight: 500;
    letter-spacing: 0.04em;
  }
  .city-sep { width: 5px; height: 5px; border-radius: 50%; background: var(--brand-red); }

  /* Back */
  .card-back { background: var(--card-white); }
  .back-brand {
    position: absolute;
    left: 40px; top: 40px;
    display: flex;
    align-items: center;
    gap: 12px;
  }
  .back-brand .brand-dot { width: 16px; height: 16px; background: var(--mark-grey); }
  .back-brand .brand-name { font-size: 22px; }
  .back-brand .brand-name span { display: block; font-size: 12px; letter-spacing: 0.18em; }
  .corner-accent {
    position: absolute;
    right: -120px; top: 60px;
    width: 300px; height: 300px;
    border-radius: 50%;
    background: var(--brand-red);
  }
  .person {
    position: absolute;
    left: 40px; top: 168px;
  }
  .person-name { color: var(--brand-red); font-size: 23px; font-weight: 700; }
  .person-title { color: var(--ink-grey); font-size: 15px; font-weight: 500; margin-top: 2px; }
  .contact-list {
    position: absolute;
    left: 40px; top: 240px;
    list-style: none;
    color: var(--ink-grey);
    font-size: 14px;
    font-weight: 500;
  }
  .contact-list li { display: flex; align-items: center; gap: 10px; height: 21px; }
  .contact-list svg { width: 14px; height: 14px; flex: none; }
</style>
</head>
<body>

<section class="card card-front" aria-label="Card front">
  <div class="front-brand">
    <div class="brand-dot"></div>
    <div class="brand-name">Harbourline<span>Supply Pty Ltd</span></div>
  </div>
  <div class="city-list">
    <span>Geelong</span><i class="city-sep"></i><span>Townsville</span><i class="city-sep"></i><span>Launceston</span>
  </div>
</section>

<section class="card card-back" aria-label="Card back">
  <div class="corner-accent"></div>
  <div class="back-brand">
    <div class="brand-dot"></div>
    <div class="brand-name">Harbourline<span>Supply Pty Ltd</span></div>
  </div>
  <div class="person">
    <div class="person-name">Desmond Varrick</div>
    <div class="person-title">General Manager</div>
  </div>
  <ul class="contact-list">
    <li>
      <svg viewBox="0 0 14 14" aria-hidden="true"><rect x="3.5" y="1" width="7" height="12" rx="1.5" fill="none" stroke="#ec1f27" stroke-width="1.5"/><circle cx="7" cy="10.8" r="0.8" fill="#ec1f27"/></svg>
      0427 561 394
    </li>
    <li>
      <svg viewBox="0 0 14 14" aria-hidden="true"><rect x="1" y="3" width="12" height="8.5" fill="#ec1f27"/><path d="M1 3 L7 8 L13 3" fill="none" stroke="#fff" stroke-width="1.2"/></svg>
      dessie@harbourlinesupply.com.au
    </li>
    <li>
      <svg viewBox="0 0 14 14" aria-hidden="true"><rect x="1" y="3" width="12" height="8.5" fill="#ec1f27"/><path d="M1 3 L7 8 L13 3" fill="none" stroke="#fff" stroke-width="1.2"/></svg>
      dessie@outbackworks.com.au
    </li>
    <li>
      <svg viewBox="0 0 14 14" aria-hidden="true"><g fill="none" stroke="#ec1f27" stroke-width="1.2"><circle cx="7" cy="7" r="6"/><ellipse cx="7" cy="7" rx="2.6" ry="6"/><path d="M1 7 H13 M2 4 H12 M2 10 H12"/></g></svg>
      www.harbourlinesupply.com.au
    </li>
  </ul>
</section>

</body>
</html>
```